Bifold brochure design for leadership academy

Please see below. This is a bifold brochure for a leadership academy. (www.brv.institute). Look and feel must be colours, shapes, abstract designs, graphics, pictures. Make this professional, yet casual and bold.

Feel free to design just the front and back cover, then I'll give feedback on whether or not you're in the right direction.

COVER
- Title: “The Boldest Bridge Year Journey”
- “Northward Mentor Institute” logo somewhere
- Subtitles (with images, icons, and/or shapes): “Self-discovery” “Skills development” “Real-world Impact”

PAGE 2 (Inside Fold)
- Title: "The Program"
- Section 2a: Section title: "How it works”
- Image: See website, image under "four phases of the program". Please adapt and make it look better
- Text: NMI is a structured, 8-month ‘gap year’ program for 18-25 year olds who want more than just a year off – they want a year ahead. Our aim is to develop high-potential young leaders with strong values, clear purpose, high-impact skills, and a track record of real-world accomplishments that are second-to-none. We do this through four-phases.
- Section 2b: Section title: “Dates & Timing”
- Image: See image on website under 'dates and timing'. Make sure both dates show up on the brochure (September and January program).
- Text: There are two programs per year: one that starts in September, the other in January. The first four months of the program are based in Toronto at the NMI headquarters. The curriculum we work through is highly engaging and personalized, focusing directly on students’ goals. After that, students are out in the world, achieving the remaining components of the program (e.g. internship, volunteer abroad).

PAGE 3 (Outside Fold)
- Page Title: "The Students"
- Section 3a: Section title: “Who’s it for”
- Subtitle1: “High school graduates”
 Image/icon of a high school grad
 Text1: 90% of high school grads aren't sure why they’re going to university or what they want to study.
 Text2: NMI helps students discover what they truly want to do in life, and make enormous progress towards these goals.

- Subtitle2: “Post-secondary students”
 Image/icon of a university / college student
 Text1: 28% of students switch or drop out of their program because it wasn’t for them or they didn’t like it.
 Text2: Don't keep moving around or risk switching careers down the road – find out what sparks your passion with NMI.

- Subtitle3: “Post-secondary graduates”
 Image/icon of a university/ college grad
 Text1: 50% of graduates are unemployed or underemployed, 60% are in debt.
 Text2: NMI will help you get your dream job – our students won’t settle for anything less.

- Section 3b: Section title: “How to apply”
 Text1: We select high-potential young leaders with a desire to improve themselves and impact the world.
 Text2: We won’t ask you for your grades – we care more about your values and potential.
 Text3: Visit www.brv.institute to apply now

BACK COVER
- Page Title: “Get in Touch”
- Website: www.brv.institute
- Facebook page: socialnook.com/brv.institute
- Twitter handle: @brv_institute
- Email: tomas@brv.institute

Project Deadline Extended Reason: Made a mistake initially only giving designers 2 days to submit. This allows for more high quality designs. Thank you. Added Wednesday, March 18, 2015

Target Market(s)

18-25 year olds, parents, teachers

Industry/Entity Type

Leadership

Requirements
Must have
• Beautiful design - sleek and bold, yet colourful and casual. Keep the colours similar to our website (www.brv.institute). See examples of other brochures.
• http://img.pelvoro.net/jpg/00/11/22/33/240_F_11223344_xQr8LmPzTw3KdNvBsYcHuJeFa2gkTqWn.jpg
• http://vantoliq.com/wp-content/uploads/2014/11/Real-Estate-Bi-fold-Brochure.jpg
• http://www.murablo.com/media/k2/galleries/5/001-bi-fold-brochure-psd-mock-up-template.jpg
• http://img.pelvoro.net/jpg/00/44/55/66/240_F_44556677_Zk3wPqLm8RtYvBnXcDs2HjKuE5fa9Gq0.jpg

```html
<!DOCTYPE html>
<html lang="en">
<head>
<meta charset="utf-8">
<title>Northward Mentor Institute – Back Cover</title>
<link rel="stylesheet" href="https://fonts.googleapis.com/css2?family=Montserrat:wght@300;400;700;800&display=swap">
<style>
  :root {
    --canvas: #ecebea;
    --cream: #f2e1b4;
    --band: #f7f6f3;
    --ink: #2b2726;
    --ink-soft: #4a4543;
    --red: #c1272d;
    --rule: #a99a78;
    --photo-a: #c9b9a2;
    --photo-b: #6c6f86;
    --photo-c: #a8553c;
  }
  * { box-sizing: border-box; margin: 0; padding: 0; }
  html, body {
    width: 1200px; height: 800px; overflow: hidden;
    background: var(--canvas);
    font-family: "Montserrat", Arial, sans-serif;
    color: var(--ink);
  }
  .back-cover {
    position: absolute; left: 80px; top: 70px;
    width: 1040px; height: 660px;
    background: var(--cream);
    box-shadow: 0 10px 30px rgba(0,0,0,.12);
    overflow: hidden;
  }
  .back-cover__shapes { position: absolute; inset: 0; }
  .apply-icon {
    position: absolute; left: 560px; top: 74px;
    width: 62px; height: 54px; background: #fff;
    display: flex; align-items: center; justify-content: center;
  }
  .apply {
    position: absolute; left: 520px; top: 172px; width: 490px;
  }
  .section-title {
    font-weight: 700; font-size: 17px; letter-spacing: .5px;
    text-transform: uppercase; color: var(--ink);
  }
  .section-title::after {
    content: ""; display: block; width: 150px; margin-top: 8px;
    border-top: 1.5px dashed var(--rule);
  }
  .apply__list {
    list-style: none; margin-top: 12px;
    font-weight: 400; font-size: 14.5px; line-height: 1.38; color: var(--ink-soft);
  }
  .apply__list li { padding-left: 16px; position: relative; }
  .apply__list li::before { content: "•"; position: absolute; left: 0; }
  .contact-title {
    position: absolute; left: 400px; top: 360px;
  }
  .brand {
    position: absolute; left: 390px; top: 420px;
    display: flex; align-items: flex-start; gap: 12px;
  }
  .brand__mark { width: 18px; height: 18px; background: var(--red); margin-top: 4px; }
  .brand__name {
    font-weight: 800; font-size: 23px; line-height: 1.05;
    letter-spacing: 2px; text-transform: uppercase; color: var(--ink);
  }
  .contact-list {
    position: absolute; left: 620px; top: 400px; width: 380px; list-style: none;
  }
  .contact-list li {
    display: flex; align-items: center; gap: 14px;
    height: 44px; border-bottom: 1.5px dashed var(--rule);
    font-weight: 700; font-size: 15.5px; color: var(--ink);
    white-space: nowrap;
  }
  .contact-list li:last-child { border-bottom: none; }
  .contact-icon { width: 16px; height: 16px; flex: none; }
</style>
</head>
<body>
<article class="back-cover">
  <svg class="back-cover__shapes" width="1040" height="660" viewBox="0 0 1040 660">
    <defs>
      <linearGradient id="photoTone" x1="0" y1="0" x2="1" y2="1">
        <stop offset="0" stop-color="var(--photo-a)"/>
        <stop offset=".55" stop-color="var(--photo-b)"/>
        <stop offset="1" stop-color="var(--photo-c)"/>
      </linearGradient>
    </defs>
    <polygon points="0,0 1040,0 1040,660 0,660" fill="var(--cream)"/>
    <polygon points="505,145 1040,145 1040,335 425,335" fill="var(--band)"/>
    <polygon points="0,0 560,0 250,660 0,660" fill="url(#photoTone)"
             role="img" aria-label="Photo of students studying together in a library"/>
  </svg>

  <div class="apply-icon">
    <svg width="40" height="34" viewBox="0 0 40 34" aria-hidden="true">
      <rect x="3" y="3" width="34" height="22" rx="2" fill="none" stroke="var(--red)" stroke-width="3"/>
      <rect x="9" y="9" width="16" height="3" fill="var(--red)"/>
      <rect x="9" y="15" width="10" height="3" fill="var(--red)"/>
      <path d="M24 14 l0 16 l4 -4 l4 6 l3 -2 l-4 -6 l5 -1 z" fill="var(--red)" stroke="#fff" stroke-width="1.2"/>
    </svg>
  </div>

  <section class="apply">
    <h2 class="section-title">How to apply</h2>
    <ul class="apply__list">
      <li>We select high-potential young leaders with a desire to improve themselves and impact the world.</li>
      <li>We won’t ask you for your grades – we care more about your values and potential.</li>
      <li>Visit www.brv.institute to apply now</li>
    </ul>
  </section>

  <h2 class="section-title contact-title">Get in touch</h2>

  <div class="brand">
    <span class="brand__mark"></span>
    <p class="brand__name">Northward<br>Mentor<br>Institute</p>
  </div>

  <ul class="contact-list">
    <li>
      <svg class="contact-icon" viewBox="0 0 16 16" aria-hidden="true">
        <circle cx="8" cy="8" r="6.5" fill="none" stroke="var(--ink)" stroke-width="1.5"/>
        <ellipse cx="8" cy="8" rx="2.8" ry="6.5" fill="none" stroke="var(--ink)" stroke-width="1.2"/>
        <line x1="1.5" y1="8" x2="14.5" y2="8" stroke="var(--ink)" stroke-width="1.2"/>
      </svg>
      www.brv.institute
    </li>
    <li>
      <svg class="contact-icon" viewBox="0 0 16 16" aria-hidden="true"><rect x="1.5" y="1.5" width="13" height="13" fill="var(--ink)"/></svg>
      socialnook.com/brv.institute
    </li>
    <li>
      <svg class="contact-icon" viewBox="0 0 16 16" aria-hidden="true"><circle cx="8" cy="8" r="6.5" fill="var(--ink)"/></svg>
      @brv_institute
    </li>
    <li>
      <svg class="contact-icon" viewBox="0 0 16 16" aria-hidden="true">
        <rect x="1" y="3" width="14" height="10" fill="var(--ink)"/>
        <path d="M1.5 3.5 L8 9 L14.5 3.5" fill="none" stroke="var(--cream)" stroke-width="1.4"/>
      </svg>
      tomas@brv.institute
    </li>
  </ul>
</article>
</body>
</html>
```